Finding the Root: Reason in Clinical Choice-Crafting

I'd like a cover that looks like it would fit on the shelf next to "The Illness Mirage" by Corwin Talley, "The Close of Forgetting" by Hugh Marchetti, "Meal Mend" by Paul Grieve, "The Energy Restart Plan" by Oscar Pemberley or "The Gland Restart Plan" by the same or "The Cortex Restart Plan" by the same ... either text only (with some interesting fonts that make the title stand out, and the subtitle smaller) or a relevant image, though I'm not entirely sure what that would be since this is a book about big-picture medical decision making.
Author name is Dr Tessa Morrow, NMD
I'll eventually request an e-book, paperback, and audio cover from the winner...

Target Market(s)

practicing physicians

Industry/Entity Type

medicine

Requirements
Must have
• look similar to other books in the genre

```html
<!DOCTYPE html>
<html lang="en">
<head>
<meta charset="utf-8">
<title>Finding the Root: Reason in Clinical Choice-Crafting</title>
<link rel="stylesheet" href="https://fonts.googleapis.com/css2?family=Bebas+Neue&family=Poppins:wght@600&display=swap">
<style>
  :root {
    --backdrop: #c9c9c9;
    --cover-green: #1a2f18;
    --accent-lime: #cdf21a;
    --title-white: #ffffff;
    --art-tint: #22401d;
  }
  html, body {
    margin: 0;
    padding: 0;
    width: 1200px;
    height: 2615px;
    overflow: hidden;
    background: var(--backdrop);
  }
  .book-cover {
    position: absolute;
    left: 80px;
    top: 527px;
    width: 1040px;
    height: 1561px;
    background: var(--cover-green);
    box-shadow: 0 18px 40px rgba(0, 0, 0, 0.28);
  }
  .cover-art {
    position: absolute;
    left: 233px;
    top: 153px;
    width: 578px;
    height: 154px;
  }
  .title-line {
    position: absolute;
    left: 0;
    width: 100%;
    margin: 0;
    text-align: center;
    font-family: "Bebas Neue", "Oswald", sans-serif;
    font-weight: 400;
    line-height: 1;
    color: var(--title-white);
    font-size: 290px;
  }
  .title-finding { top: 337px; }
  .title-the { top: 571px; }
  .title-root { top: 804px; color: var(--accent-lime); }
  .subtitle {
    position: absolute;
    left: 0;
    top: 1078px;
    width: 100%;
    margin: 0;
    text-align: center;
    font-family: "Bebas Neue", "Oswald", sans-serif;
    font-weight: 400;
    font-size: 60px;
    line-height: 61px;
    letter-spacing: 0.12em;
    color: var(--title-white);
  }
  .subtitle-line { display: block; }
  .subtitle-accent { color: var(--accent-lime); }
  .author-name {
    position: absolute;
    left: 0;
    top: 1414px;
    width: 100%;
    margin: 0;
    text-align: center;
    font-family: "Poppins", "Helvetica", sans-serif;
    font-weight: 600;
    font-size: 30px;
    letter-spacing: 0.14em;
    color: var(--title-white);
  }
</style>
</head>
<body>
  <main class="book-cover">
    <svg class="cover-art" role="img" aria-label="Line drawing of a brain trailing a winding path to branching direction arrows" viewBox="0 0 578 154">
      <rect x="0" y="0" width="578" height="154" rx="20" fill="var(--art-tint)"/>
    </svg>
    <h1 class="title-line title-finding">FINDING</h1>
    <p class="title-line title-the">THE</p>
    <p class="title-line title-root">ROOT</p>
    <h2 class="subtitle">
      <span class="subtitle-line">REASON IN</span>
      <span class="subtitle-line">CLINICAL</span>
      <span class="subtitle-line subtitle-accent">CHOICE-CRAFTING</span>
    </h2>
    <p class="author-name">DR TESSA MORROW, NMD</p>
  </main>
</body>
</html>
```